Simple Postcard Design

We want to have Prenta do a mailing for our new real estate company. We have roughed a sketch of what we would like. A picture of the property on one side and the copy on the reverse side.Attached are the files.

POSTCARD Size-8.52" x 5.47" **********

Target Market(s)

Residents of our town

Industry/Entity Type

Real Estate

Font styles to use
Serif

Colors
00a990

Requirements
Must have
• Look of elegance
Nice to have
• NO NO Border on picture,,,,,banner on 45 in top left corner
• "New Listing"

```html
<!DOCTYPE html>
<html lang="en">
<head>
<meta charset="utf-8">
<title>New Listing Postcard – Bayhaven Realtors</title>
<link rel="stylesheet" href="https://fonts.googleapis.com/css2?family=Tinos:ital,wght@0,400;0,700;1,400&display=swap">
<style>
  :root {
    --page-bg: #ecebe8;
    --card: #ffffff;
    --brand-green: #0f5a34;
    --brand-gold: #e6b450;
    --ink: #111111;
    --rule: #bdbdbd;
    --shadow: rgba(0,0,0,0.28);
  }
  * { margin: 0; padding: 0; box-sizing: border-box; }
  html, body { width: 918px; height: 1200px; overflow: hidden; }
  body {
    position: relative;
    background: var(--page-bg);
    font-family: "Tinos", "Times New Roman", serif;
    color: var(--ink);
  }
  .postcard {
    position: absolute;
    width: 712px;
    height: 512px;
    background: var(--card);
    box-shadow: 6px 8px 14px var(--shadow);
  }
  .postcard--front { left: 63px; top: 55px; }
  .postcard--back { left: 128px; top: 613px; }

  .property-photo {
    position: absolute;
    left: 19px; top: 15px;
    width: 673px; height: 481px;
    border-radius: 12px;
    background:
      radial-gradient(ellipse 38% 30% at 48% 55%, #cdb79a 0%, #b9a184 55%, transparent 75%),
      radial-gradient(ellipse 45% 35% at 80% 30%, #8e8f8a 0%, transparent 70%),
      linear-gradient(160deg, #1c2b3b 0%, #243447 35%, #1a2532 60%, #2f3f3a 100%);
  }

  .listing-banner {
    position: absolute;
    left: 0; top: 31px;
    width: 238px; height: 76px;
  }
  .listing-banner__text {
    position: absolute;
    left: 0; top: 0;
    width: 238px; height: 76px;
    line-height: 76px;
    padding-left: 42px;
    font-size: 30px;
    color: var(--brand-gold);
  }

  .brand-name {
    position: absolute;
    left: 37px; top: 42px;
    font-size: 30px;
    color: var(--brand-green);
    letter-spacing: 0.5px;
  }
  .contact {
    position: absolute;
    left: 37px; top: 139px;
    font-size: 14px;
    line-height: 17px;
  }
  .listing-copy {
    position: absolute;
    left: 37px; top: 233px;
    width: 324px;
    font-size: 15.5px;
    line-height: 18.6px;
    text-align: justify;
  }
  .disclaimer {
    position: absolute;
    left: 37px; top: 397px;
    width: 336px;
    font-size: 12px;
    line-height: 17px;
    font-style: italic;
  }
  .stamp-box {
    position: absolute;
    left: 589px; top: 40px;
    width: 91px; height: 62px;
    border: 1.5px solid var(--rule);
  }
  .address-lines {
    position: absolute;
    left: 450px; top: 176px;
    width: 239px;
  }
  .address-lines span {
    display: block;
    height: 1.5px;
    background: var(--rule);
    margin-bottom: 27.5px;
  }
</style>
</head>
<body>
  <section class="postcard postcard--front">
    <div class="property-photo" role="img" aria-label="Aerial photograph of the waterfront estate on a bayside point with pool, dock and neighbouring homes along a canal"></div>
    <div class="listing-banner">
      <svg width="238" height="76" viewBox="0 0 238 76" aria-hidden="true">
        <polygon points="0,0 238,0 228,38 238,76 0,76" fill="#0f5a34"/>
        <polyline points="0,5 231,5" stroke="#e6b450" stroke-width="1.5" fill="none"/>
        <polyline points="0,71 231,71" stroke="#e6b450" stroke-width="1.5" fill="none"/>
      </svg>
      <div class="listing-banner__text">New Listing</div>
    </div>
  </section>

  <section class="postcard postcard--back">
    <div class="brand-name">Bayhaven Realtors</div>
    <address class="contact" style="font-style: normal;">
      BAYHAVEN REALTORS<br>
      48 Shoreline Avenue<br>
      Bayhaven, NJ 08700<br>
      555 014-2200<br>
      www.BayhavenRealtors.com
    </address>
    <p class="listing-copy">This unique 1.68 acre estate in Bayhaven has 644' of water front. The 22 room house features a 2 story master suite, 6 guest bedrooms, large living room, great room with 2 fireplaces, in law Suite, 15 car garage, in ground pool, brick patio, numerous porches and a 200' Dock.<br>Priced at $4,995,000</p>
    <p class="disclaimer">If your property is listed with a real estate broker, please disregard. It is not our intention to solicit the offerings of other real estate brokers.</p>
    <div class="stamp-box"></div>
    <div class="address-lines"><span></span><span></span><span></span><span></span><span></span></div>
  </section>
</body>
</html>
```